Corbell Lending Partners - Real estate loans - need a business card with a logo

I need a logo and a business card that looks elegant - that looks as if it is a big stablish corporation - We do real estate loans, my goal is to brand myself with colors black background - gold or silver letters - some combination - Name of the company different color than the rest of the card -

```html
<!DOCTYPE html>
<html lang="en">
<head>
<meta charset="utf-8">
<title>Corbell Lending Partners – Business Card</title>
<link rel="stylesheet" href="https://fonts.googleapis.com/css2?family=Montserrat:wght@400;600&display=swap">
<style>
  :root {
    --backdrop: #1c1c1d;
    --card: #0b0b0c;
    --gold: #d8bd78;
    --silver: #e4e4e4;
    --muted: #c9c9c9;
  }
  * { box-sizing: border-box; margin: 0; padding: 0; }
  html, body { width: 1200px; height: 890px; overflow: hidden; }
  body {
    background: var(--backdrop);
    font-family: "Montserrat", Arial, sans-serif;
    display: flex;
    align-items: center;
    justify-content: center;
    gap: 90px;
  }
  .card {
    width: 400px;
    height: 640px;
    background: var(--card);
    border-radius: 18px;
    display: flex;
    flex-direction: column;
    align-items: center;
    box-shadow: 0 20px 50px rgba(0,0,0,.55);
  }
  .card--back { justify-content: center; padding-bottom: 60px; }
  .card--front { padding-top: 110px; }

  .brand-name {
    color: var(--gold);
    font-weight: 600;
    font-size: 22px;
    letter-spacing: 3px;
    text-transform: uppercase;
    text-align: center;
    line-height: 1.45;
  }

  .person { margin-top: 56px; text-align: center; }
  .person__name {
    color: var(--gold);
    font-weight: 600;
    font-size: 25px;
    letter-spacing: 1px;
    text-transform: uppercase;
  }
  .person__role {
    color: var(--silver);
    font-weight: 400;
    font-size: 16px;
    letter-spacing: 1px;
    margin-top: 4px;
  }

  .contact-icons {
    display: flex;
    gap: 16px;
    margin-top: 26px;
  }
  .contact-icons svg { width: 22px; height: 22px; fill: var(--gold); }

  .contact {
    list-style: none;
    margin-top: 16px;
    text-align: center;
    color: var(--muted);
    font-size: 16px;
    line-height: 1.45;
    letter-spacing: .5px;
  }
  .contact__address { margin-top: 14px; }
</style>
</head>
<body>
  <section class="card card--back" aria-label="Card back">
    <p class="brand-name">Corbell Lending<br>Partners</p>
  </section>

  <section class="card card--front" aria-label="Card front">
    <p class="brand-name">Corbell Lending<br>Partners</p>

    <div class="person">
      <h1 class="person__name">Marcus Delane</h1>
      <p class="person__role">Managing Director</p>
    </div>

    <div class="contact-icons">
      <svg viewBox="0 0 24 24" aria-label="Phone"><path d="M6.6 10.8a15.1 15.1 0 0 0 6.6 6.6l2.2-2.2c.3-.3.7-.4 1-.2 1.1.4 2.3.6 3.6.6.6 0 1 .4 1 1V20c0 .6-.4 1-1 1A17 17 0 0 1 3 4c0-.6.4-1 1-1h3.5c.6 0 1 .4 1 1 0 1.3.2 2.5.6 3.6.1.3 0 .7-.2 1z"/></svg>
      <svg viewBox="0 0 24 24" aria-label="Email"><path d="M2 5h20v14H2z M3.5 6.5v.4L12 13l8.5-6.1v-.4z" fill-rule="evenodd"/></svg>
      <svg viewBox="0 0 24 24" aria-label="Website"><path d="M12 2a10 10 0 1 0 0 20 10 10 0 0 0 0-20zm0 2c1 0 2.3 2.2 2.7 6H9.3C9.7 6.2 11 4 12 4zm-2.7 8h5.4c-.4 3.8-1.7 6-2.7 6s-2.3-2.2-2.7-6zM4.1 10a8 8 0 0 1 3.6-5.1A14 14 0 0 0 7.3 10zm0 2h3.2c.1 2 .5 3.7 1.1 5.1A8 8 0 0 1 4.1 12zm12.6-2a14 14 0 0 0-.4-5.1 8 8 0 0 1 3.6 5.1zm0 2h3.2a8 8 0 0 1-4.3 5.1c.6-1.4 1-3.1 1.1-5.1z"/></svg>
    </div>

    <ul class="contact">
      <li>+19055550142</li>
      <li>mdelane@corbell.com</li>
      <li>www.corbell.com</li>
      <li class="contact__address">48 Harbour Crest Lane,<br>Maple Ridge, ON L6K</li>
    </ul>
  </section>
</body>
</html>
```